Front and content page design for Fitness Cookbook

I am looking for someone to Design a front cover for a Recipe book and also create an amazing layout for the book.

Its for a corporate seminar so has to be eye catching, professional and bold.

Content is complete

Target Market(s)

Industry/Entity Type

Health And Wellness

Font styles to use
Sans Serif

Requirements
Must have
• Eye catching, professional and bold.
• By Dorian as stated on the document
• Must have Tidewell Motion Logo on it.

```html
<!DOCTYPE html>
<html lang="en">
<head>
<meta charset="utf-8">
<title>Protein and Carbohydrate Meals</title>
<link href="https://fonts.googleapis.com/css2?family=Cabin:wght@400;500;600&display=swap" rel="stylesheet">
<style>
  :root {
    --brand-blue: #1f8fd2;
    --ink: #1b1b1b;
    --tab-orange: #f7a21b;
    --paper: #ffffff;
  }
  html, body {
    margin: 0;
    padding: 0;
    overflow: hidden;
    background: var(--paper);
  }
  .page {
    position: relative;
    width: 849px;
    height: 1200px;
    overflow: hidden;
    background: var(--paper);
    font-family: "Cabin", "Gill Sans", sans-serif;
    color: var(--ink);
  }
  .chapter-title {
    position: absolute;
    top: 92px;
    left: 0;
    width: 849px;
    margin: 0;
    text-align: center;
    font-weight: 400;
    font-size: 62px;
    line-height: 76px;
    color: var(--brand-blue);
  }
  .section-tab {
    position: absolute;
    right: 0;
    top: 277px;
    width: 34px;
    height: 232px;
    background: var(--tab-orange);
  }
  .info-block {
    position: absolute;
    left: 57px;
    width: 700px;
  }
  .info-block.best-used { top: 300px; }
  .info-block.why-eat { top: 421px; }
  .info-heading {
    margin: 0 0 6px;
    font-size: 31px;
    line-height: 34px;
    font-weight: 500;
    color: var(--brand-blue);
  }
  .info-list {
    list-style: none;
    margin: 0;
    padding: 0;
    font-size: 19px;
    line-height: 24.5px;
    font-weight: 500;
  }
  .info-list li::before {
    content: "\2022";
    margin-right: 6px;
  }
  .page-footer {
    position: absolute;
    right: 18px;
    bottom: 44px;
    display: flex;
    align-items: center;
    gap: 12px;
    font-size: 13px;
  }
  .footer-brand {
    display: flex;
    align-items: center;
    gap: 4px;
    color: var(--brand-blue);
    font-weight: 600;
    font-size: 11px;
  }
  .footer-brand .mark {
    width: 9px;
    height: 9px;
    background: var(--brand-blue);
  }
  .page-number { color: var(--ink); }
</style>
</head>
<body>
  <div class="page">
    <h1 class="chapter-title">Protein and<br>Carbohydrate Meals</h1>

    <div class="section-tab"></div>

    <section class="info-block best-used">
      <h2 class="info-heading">BEST USED</h2>
      <ul class="info-list">
        <li>Before and/or after training</li>
        <li>Before bed</li>
        <li>During a high carb or muscle building phase</li>
      </ul>
    </section>

    <section class="info-block why-eat">
      <h2 class="info-heading">WHY EAT THESE MEALS</h2>
      <ul class="info-list">
        <li>To promote muscle growth</li>
        <li>To provide fuel for training</li>
        <li>To aid recovery from training</li>
        <li>To help relax before bed and improve sleep quality</li>
      </ul>
    </section>

    <footer class="page-footer">
      <span class="footer-brand"><span class="mark"></span>Tidewell Motion</span>
      <span class="page-number">11</span>
    </footer>
  </div>
</body>
</html>
```